Velour Detailing – Premium Automotive Detailing Studio Website Design

We're launching a premium automotive detailing studio called Velour Detailing, and we’re looking for a clean, minimal, and high-end website design (desktop + mobile version). The studio targets owners of luxury vehicles who care deeply about aesthetics, perfection, and exceptional service.
This project is about more than just showing services , it should feel like a luxury experience from the very first second. The design should be modern, minimalistic, elegant, and clearly aimed at an upscale market.
We’re looking for a designer who can translate our physical studio’s premium interior and architectural feel into a digital presence.
What we want the website to feel like:
Clean and modern
Professional and luxurious
Minimal and not cluttered
Light animations or transitions to add polish
Stylish and cinematic
Design freedom:
We trust your design direction. We are not providing strict color codes or layout instructions, we want you to create what you believe works best based on our brand positioning and target audience. Just keep it premium, modern, and well-organized.
What the website should include:
Hero section with a bold visual (image or video)
About the Studio — a few blocks explaining our story and focus on quality
Service Overview — clearly showing what we offer (detailing, ceramic coating, interior, etc.)
Gallery/Showcase — show off our work with cars, interior, and the space itself
Client Lounge Area — mention comfort, coffee, and waiting space
Testimonials — social proof from satisfied clients
Location & contact section — map, address, contact form
Footer, simple with nav, contact info, and optional social media
Target audience:
Owners of high-end vehicles (Valtrane, Korvel, etc.)
Car collectors and detailing enthusiasts
People looking for premium-level service and presentation
Brands/creators booking our photo studio

```html
<!DOCTYPE html>
<html lang="en">
<head>
<meta charset="utf-8">
<title>Velour Detailing – Premium Automotive Detailing Studio</title>
<link href="https://fonts.googleapis.com/css2?family=Montserrat:wght@400;500;600;700;800;900&display=swap" rel="stylesheet">
<style>
:root{
  --gold:#b88a35;
  --gold-light:#d4a64c;
  --gold-dark:#9b7027;
  --ink:#141414;
  --paper:#efefef;
  --white:#ffffff;
  --text:#2b2b2b;
  --muted:#6b6b6b;
}
*{box-sizing:border-box;margin:0;padding:0}
html,body{width:1200px;height:5376px;overflow:hidden}
body{font-family:'Montserrat',sans-serif;background:var(--paper);color:var(--text);position:relative}
.abs{position:absolute}
.brand{font-family:'Montserrat',sans-serif;font-weight:800;letter-spacing:1px;line-height:1;display:flex;align-items:center;gap:12px}
.brand-mark{width:26px;height:26px;border:3px solid currentColor}
.brand small{display:block;font-size:.42em;letter-spacing:.55em;margin-top:4px}
/* nav */
.nav{position:absolute;top:0;left:0;width:1200px;height:98px;background:var(--white);z-index:2}
.nav .brand{position:absolute;left:73px;top:30px;font-size:26px;color:var(--ink)}
.nav-links{position:absolute;left:295px;top:38px;font-size:14px;font-weight:500;color:#444}
.nav-links a{text-decoration:none;color:inherit;position:absolute;white-space:nowrap}
.nav-links a.active{color:var(--gold)}
.nav-links a.active::after{content:"";display:block;height:2px;background:var(--gold);margin-top:5px}
.btn-gold{position:absolute;background:linear-gradient(180deg,var(--gold-light),var(--gold-dark));color:#fff;font-weight:600;font-size:14px;border-radius:10px;display:flex;align-items:center;justify-content:center}
/* hero */
.hero{position:absolute;top:98px;left:0;width:1200px;height:543px;background:linear-gradient(90deg,#5a3a28 0%,#2a1e1a 28%,#141418 55%,#0d0f16 100%)}
.hero-band{position:absolute;top:641px;left:0;width:1200px;height:8px;background:var(--gold)}
.hero-title{position:absolute;left:597px;top:200px;font-size:40px;font-weight:900;color:#fff;letter-spacing:.5px;white-space:nowrap;line-height:48px}
.hero-frame{position:absolute;left:601px;top:271px;width:328px;height:205px;border:2px solid var(--gold);border-right:none}
.hero-frame p{position:absolute;left:24px;font-size:38px;font-weight:900;color:#fff;line-height:1}
.btn-outline{position:absolute;left:601px;top:520px;width:262px;height:48px;border:2px solid #fff;border-radius:10px;color:#fff;font-size:14px;font-weight:500;display:flex;align-items:center;justify-content:center}
/* headings */
.sec-title{position:absolute;font-size:30px;font-weight:900;color:var(--ink);text-transform:uppercase;white-space:nowrap}
.sec-title em{font-style:normal;color:var(--gold)}
.sec-title.light{color:#fff}
.rule{position:absolute;height:3px;background:var(--gold)}
/* about */
.about-text{position:absolute;left:113px;top:822px;width:455px;font-size:14px;line-height:31px;color:#333}
.about-text b{font-weight:700;color:var(--ink)}
.vdivider{position:absolute;left:601px;top:747px;width:2px;height:375px;background:var(--gold)}
.photo{position:absolute;border-radius:8px}
/* services */
.services{position:absolute;top:1242px;left:0;width:1200px;height:845px;background:linear-gradient(135deg,#1a1a1a,#0f0f0f)}
.card{position:absolute;width:288px;height:275px;background:#fff;border-radius:10px;padding:30px 24px}
.card svg{display:block;margin-bottom:16px}
.card h3{font-size:19px;font-weight:600;color:var(--ink);margin-bottom:14px;line-height:25px}
.card p{font-size:13px;line-height:22px;color:var(--muted)}
/* gallery */
.tile{position:absolute;border-radius:8px}
.play{position:absolute;left:411px;top:2440px;width:46px;height:46px;border-radius:50%;background:#c9802a;display:flex;align-items:center;justify-content:center}
.tile-brand{color:#fff;font-size:38px;flex-direction:column;gap:8px}
/* lounge */
.lounge{position:absolute;top:3085px;left:0;width:1200px;height:572px;background:#0c0c0d}
.lounge-list{position:absolute;left:133px;top:3258px;list-style:none;width:470px}
.lounge-list li{position:relative;padding-left:24px;font-size:18px;color:#fff;line-height:24px}
.lounge-list li::before{content:"»";position:absolute;left:0;color:var(--gold);font-weight:700}
/* testimonials */
.quote{position:absolute;width:463px;height:258px;background:#fff;border-radius:10px;box-shadow:0 4px 18px rgba(0,0,0,.08);padding:38px 30px}
.quote p{font-size:14px;line-height:25px;color:#444}
.avatar{position:absolute;left:28px;top:168px;width:62px;height:62px;border-radius:50%}
.quote .who{position:absolute;left:104px;top:176px;font-size:16px;line-height:24px;color:#333}
.stars{position:absolute;top:186px;display:flex;gap:4px}
.arrow{position:absolute;top:3972px;font-size:34px;color:#222;font-weight:500}
/* contact */
.contact{position:absolute;left:111px;top:4210px;width:980px;height:580px;background:linear-gradient(135deg,#1a1a1a,#0b0b0b 60%,#1c1c1c);border-radius:12px}
.addr-card{position:absolute;left:185px;top:4495px;width:265px;height:95px;background:#fff;border-radius:4px;box-shadow:0 2px 8px rgba(0,0,0,.25);padding:12px 14px}
.addr-card h4{font-size:13px;font-weight:700;color:var(--gold);margin-bottom:6px}
.addr-card p{font-size:13px;line-height:20px;color:#333}
.field{position:absolute;left:603px;width:442px;height:46px;background:#fff;border-radius:8px;font-size:13px;color:#555;padding:0 18px;display:flex;align-items:center;justify-content:space-between}
/* footer */
.footer{position:absolute;top:4873px;left:0;width:1200px;height:503px;background:#121212;border-top:9px solid var(--gold)}
.footer .brand{position:absolute;left:113px;top:110px;font-size:36px;color:#fff}
.footer h5{position:absolute;font-size:16px;font-weight:700;color:var(--gold);text-transform:uppercase}
.foot-rule{position:absolute;height:2px;width:86px;background:var(--gold)}
.foot-links{position:absolute;left:525px;top:165px;list-style:none}
.foot-links li{font-size:14px;color:#ddd;line-height:38px}
.foot-info{position:absolute;left:830px;top:0;list-style:none;width:270px}
.foot-info li{display:flex;gap:10px;font-size:14px;line-height:24px;color:#ddd;position:absolute;left:0;width:270px}
.social{position:absolute;top:230px;width:32px;height:32px;border-radius:50%;background:var(--gold)}
.copy{position:absolute;left:0;top:469px;width:1200px;text-align:center;font-size:13px;color:#ccc}
</style>
</head>
<body>

<header class="nav">
  <div class="brand"><span class="brand-mark"></span><span>VELOUR<small>DETAILING</small></span></div>
  <nav class="nav-links">
    <a class="active" style="left:0">HOME</a>
    <a style="left:90px">ABOUT</a>
    <a style="left:187px">SERVICES</a>
    <a style="left:305px">GALLERY</a>
    <a style="left:417px">TESTIMONIALS</a>
    <a style="left:574px">CONTACT</a>
  </nav>
  <div class="btn-gold" style="left:965px;top:25px;width:167px;height:47px">GET STARTED</div>
</header>

<section class="hero" role="img" aria-label="Dark luxury SUV in a moody studio with warm reflections"></section>
<div class="hero-band"></div>
<h1 class="hero-title">VELOUR DETAILING</h1>
<div class="hero-frame">
  <p style="top:30px">PRECISION</p>
  <p style="top:85px">PERFECTION</p>
  <p style="top:140px">PRESTIGE</p>
</div>
<div class="btn-outline">BOOK AN APPOINTMENT</div>

<!-- About -->
<div class="rule" style="left:113px;top:747px;width:134px"></div>
<h2 class="sec-title" style="left:113px;top:773px">About the <em>Studio</em></h2>
<p class="about-text"><b>At Velour Detailing, we don't just clean cars — we transform them.</b> Our studio was built for those who appreciate the art of automotive perfection. Every surface, every contour, every detail is treated with obsessive care using the finest tools and products in the industry. Whether it's a vintage classic or a brand-new supercar, our mission remains the same: to elevate your vehicle to its highest possible standard — visually, materially, and experientially.</p>
<div class="vdivider"></div>
<div class="photo" style="left:632px;top:747px;width:458px;height:375px;background:linear-gradient(120deg,#d9dcdf,#8f969c 45%,#1b1b1f 70%,#5a1a14)" role="img" aria-label="Detailer polishing the rear of a black car in a bright studio"></div>

<!-- Services -->
<section class="services">
  <div class="rule" style="left:535px;top:62px;width:130px"></div>
  <h2 class="sec-title light" style="left:0;width:1200px;text-align:center;top:75px">Our <em>Services</em></h2>
</section>
<div class="card" style="left:113px;top:1415px">
  <svg width="66" height="62" viewBox="0 0 66 62" fill="none" stroke="#b88a35" stroke-width="2"><path d="M6 44h54v10H6zM12 44l8-16h26l8 16"/><circle cx="18" cy="54" r="5"/><circle cx="48" cy="54" r="5"/><path d="M10 10l3 6M16 6v7M22 10l-3 6"/></svg>
  <h3>Exterior Detailing</h3>
  <p>Restore brilliance and protect every curve. From hand washes to deep decontamination, we treat every surface like art.</p>
</div>
<div class="card" style="left:458px;top:1415px">
  <svg width="66" height="62" viewBox="0 0 66 62" fill="none" stroke="#b88a35" stroke-width="2"><rect x="8" y="8" width="50" height="14" rx="3"/><rect x="12" y="28" width="42" height="22" rx="4"/><circle cx="24" cy="39" r="5"/><circle cx="42" cy="39" r="5"/></svg>
  <h3>Interior Detailing</h3>
  <p>Precision cleaning and conditioning of every material — leather, fine suede, carbon fiber, and more — restoring your cabin</p>
</div>
<div class="card" style="left:802px;top:1415px">
  <svg width="66" height="62" viewBox="0 0 66 62" fill="none" stroke="#b88a35" stroke-width="2"><path d="M6 44c0-10 8-14 16-14l8-8h12l8 8c8 0 10 6 10 14z"/><circle cx="20" cy="46" r="5"/><circle cx="46" cy="46" r="5"/><circle cx="33" cy="10" r="6"/></svg>
  <h3>Ceramic Coating</h3>
  <p>Long-lasting protection with ultra-gloss finish. Our multi-year ceramic coatings enhance shine and shield against the elements.</p>
</div>
<div class="card" style="left:113px;top:1713px">
  <svg width="66" height="62" viewBox="0 0 66 62" fill="none" stroke="#b88a35" stroke-width="2"><rect x="8" y="24" width="44" height="26" rx="4"/><circle cx="20" cy="50" r="5"/><circle cx="42" cy="50" r="5"/><path d="M44 6v16M50 10v10"/></svg>
  <h3>Paint Correction</h3>
  <p>Swirl removal, scratch reduction, and mirror-like finishes. Perfected under studio lighting with surgical precision.</p>
</div>
<div class="card" style="left:458px;top:1713px">
  <svg width="66" height="62" viewBox="0 0 66 62" fill="none" stroke="#b88a35" stroke-width="2"><circle cx="24" cy="22" r="14"/><circle cx="24" cy="22" r="5"/><circle cx="44" cy="42" r="12"/><circle cx="44" cy="42" r="4"/></svg>
  <h3>Wheels &amp; Caliper Detailing</h3>
  <p>Deep cleaning and protection of wheels, barrels, and calipers — often overlooked, never by us.</p>
</div>
<div class="card" style="left:802px;top:1713px">
  <svg width="66" height="62" viewBox="0 0 66 62" fill="none" stroke="#b88a35" stroke-width="2"><circle cx="20" cy="12" r="7"/><circle cx="36" cy="12" r="7"/><rect x="8" y="22" width="36" height="22" rx="3"/><path d="M44 28l12-6v22l-12-6"/><path d="M18 44l-4 12M34 44l4 12"/></svg>
  <h3>Studio Photography &amp; Brand Shoots</h3>
  <p>Our facility doubles as a private photo studio — book sessions for content creation, product shoots, or brand activations.</p>
</div>

<!-- Gallery -->
<div class="rule" style="left:487px;top:2196px;width:136px"></div>
<h2 class="sec-title" style="left:0;width:1200px;text-align:center;top:2209px">Our <em>Gallery</em></h2>
<div class="tile" style="left:111px;top:2303px;width:648px;height:322px;background:linear-gradient(135deg,#3a3a3c,#d9d9db 45%,#9a9a9c 70%,#2a2a2c)" role="img" aria-label="White convertible sports car in the detailing studio"></div>
<div class="play"><svg width="16" height="18" viewBox="0 0 16 18"><path d="M2 1l13 8-13 8z" fill="#fff"/></svg></div>
<div class="tile brand tile-brand" style="left:771px;top:2303px;width:318px;height:322px;background:linear-gradient(135deg,#2b2c30,#3b3d42 50%,#222326);justify-content:center"><span>VELOUR</span><span style="font-size:18px;letter-spacing:9px">DETAILING</span></div>
<div class="tile" style="left:111px;top:2637px;width:318px;height:323px;background:linear-gradient(135deg,#1b2d6a,#274a9c 45%,#0d1222)" role="img" aria-label="Machine polisher on blue car paint"></div>
<div class="tile" style="left:442px;top:2637px;width:317px;height:323px;background:linear-gradient(135deg,#2a0d10,#a8131f 40%,#2b2b2e 75%)" role="img" aria-label="Red car wheel and fender close-up"></div>
<div class="tile" style="left:771px;top:2637px;width:318px;height:323px;background:linear-gradient(160deg,#18191c,#7e8388 50%,#2a2c30)" role="img" aria-label="Grey sedan front view under studio lights"></div>

<!-- Lounge -->
<section class="lounge">
  <div class="abs" style="left:600px;top:0;width:600px;height:572px;background:linear-gradient(200deg,#0c0c0d 20%,#6e0f16 55%,#1a0a0c 80%,#0c0c0d)" role="img" aria-label="Red luxury coupe in a dark showroom"></div>
  <h2 class="sec-title light" style="left:113px;top:65px;font-size:32px;line-height:48px">Relax while we perfect<br><em>your vehicle</em></h2>
</section>
<ul class="lounge-list">
  <li style="margin-bottom:22px">Italian espresso bar with gourmet coffee options</li>
  <li style="margin-bottom:22px">Comfortable seating with minimalist, modern décor</li>
  <li style="margin-bottom:22px">Viewing window into the detailing studio</li>
  <li style="margin-bottom:22px">Curated automotive magazines and digital entertainment</li>
  <li style="margin-bottom:20px">Ambient music and climate control</li>
  <li>Private WiFi access</li>
</ul>

<!-- Testimonials -->
<div class="rule" style="left:535px;top:3705px;width:130px"></div>
<h2 class="sec-title" style="left:0;width:1200px;text-align:center;top:3767px">Client <em>Testimonials</em></h2>
<div class="arrow" style="left:60px">«</div>
<div class="arrow" style="left:1108px">»</div>
<svg width="0" height="0" style="position:absolute"><defs><path id="star" d="M9 0l2.6 5.6 6.1.7-4.5 4.2 1.2 6.1L9 13.6 3.6 16.6l1.2-6.1L.3 6.3l6.1-.7z"/></defs></svg>
<div class="quote" style="left:113px;top:3862px">
  <p>"I brought in my Korvel R9 Turbo expecting a great detail — what I received was far beyond that. The finish, the reflections, the feel of the paint… it was like seeing my car for the first time again.</p>
  <div class="avatar" style="background:linear-gradient(135deg,#3a4a6a,#1f2940)" role="img" aria-label="Client portrait"></div>
  <div class="who">— R. Mehra,<br>Korvel R9 GT</div>
  <div class="stars" style="left:306px">
    <svg width="100" height="18" viewBox="0 0 100 18" fill="#d9a21b"><use href="#star"/><use href="#star" x="20"/><use href="#star" x="40"/><use href="#star" x="60"/><use href="#star" x="80"/></svg>
  </div>
</div>
<div class="quote" style="left:618px;top:3862px">
  <p>"What really sets Velour apart is the experience. I waited in the lounge with a fresh espresso while watching the process through the viewing glass. Not only was my Havick S5 restored to perfection —</p>
  <div class="avatar" style="background:linear-gradient(135deg,#a8743a,#5a3518)" role="img" aria-label="Client portrait"></div>
  <div class="who">— N. Kapoor,<br>Ardent Vesta SV</div>
  <div class="stars" style="left:306px">
    <svg width="100" height="18" viewBox="0 0 100 18" fill="#d9a21b"><use href="#star"/><use href="#star" x="20"/><use href="#star" x="40"/><use href="#star" x="60"/><use href="#star" x="80"/></svg>
  </div>
</div>

<!-- Contact -->
<section class="contact">
  <h2 class="sec-title light" style="left:0;width:980px;text-align:center;top:78px">Let's elevate your <em>drive</em></h2>
</section>
<div class="abs" style="left:156px;top:4374px;width:421px;height:336px;border-radius:8px;background:linear-gradient(135deg,#eef0f2,#dfe3e8 50%,#e9e6df)" role="img" aria-label="Street map showing the studio location"></div>
<svg class="abs" style="left:328px;top:4452px" width="22" height="30" viewBox="0 0 22 30"><path d="M11 0C5 0 0 5 0 11c0 8 11 19 11 19s11-11 11-19C22 5 17 0 11 0z" fill="#d32f2f"/><circle cx="11" cy="11" r="4" fill="#8a1c1c"/></svg>
<div class="addr-card">
  <h4>VELOUR DETAILING STUDIO</h4>
  <p>27 LUMEN AVENUE, SECTOR 9<br>AURELIA CITY 40210</p>
</div>
<div class="field" style="top:4376px">Full Name</div>
<div class="field" style="top:4452px">Phone Number</div>
<div class="field" style="top:4528px">Vehicle Make &amp; Model</div>
<div class="field" style="top:4604px">Service Interest <svg width="14" height="8" viewBox="0 0 14 8"><path d="M1 1l6 6 6-6" stroke="#333" stroke-width="1.6" fill="none"/></svg></div>
<div class="btn-gold" style="left:730px;top:4683px;width:190px;height:47px">SEND MESSAGE</div>

<!-- Footer -->
<footer class="footer">
  <div class="brand"><span class="brand-mark"></span><span>VELOUR<small>DETAILING</small></span></div>
  <p class="abs" style="left:113px;top:178px;font-size:16px;font-weight:700;color:#fff;line-height:25px">PRECISION. PERFECTION.<br>PRESTIGE.</p>
  <div class="social" style="left:113px"></div>
  <div class="social" style="left:158px"></div>
  <div class="social" style="left:203px"></div>
  <div class="social" style="left:248px"></div>

  <h5 style="left:525px;top:100px">Quick Links</h5>
  <div class="foot-rule" style="left:525px;top:128px"></div>
  <ul class="foot-links">
    <li>HOME</li><li>ABOUT</li><li>SERVICES</li><li>GALLERY</li><li>TESTIMONIALS</li><li>CONTACT</li>
  </ul>

  <h5 style="left:830px;top:100px">Contact Info</h5>
  <div class="foot-rule" style="left:830px;top:128px"></div>
  <ul class="foot-info">
    <li style="top:165px"><svg width="14" height="18" viewBox="0 0 14 18" style="flex:none;margin-top:3px"><path d="M7 0C3 0 0 3 0 7c0 5 7 11 7 11s7-6 7-11c0-4-3-7-7-7z" fill="#b88a35"/><circle cx="7" cy="7" r="2.5" fill="#121212"/></svg><span>Velour Detailing Studio, 27 Lumen Avenue, Sector 9, Aurelia City 40210</span></li>
    <li style="top:264px"><svg width="16" height="16" viewBox="0 0 16 16" style="flex:none;margin-top:4px"><path d="M3 1l3 3-2 2c1 2 3 4 5 5l2-2 3 3-2 3C7 15 1 9 1 3z" fill="#b88a35"/></svg><span>+00 555 014 2290</span></li>
    <li style="top:303px"><svg width="16" height="12" viewBox="0 0 16 12" style="flex:none;margin-top:6px"><rect width="16" height="12" rx="1" fill="#b88a35"/><path d="M1 1l7 6 7-6" stroke="#121212" stroke-width="1.4" fill="none"/></svg><span>hello@velourdetailing.example</span></li>
  </ul>

  <div class="abs" style="left:0;top:448px;width:1200px;height:1px;background:#444"></div>
  <p class="copy">© 2025 Velour Detailing. All rights reserved.</p>
</footer>

</body>
</html>
```